We are a physical therapy billing company. We need a postcard style flyer.

See attached. We are trying to generate more business for our physical therapy billing company. Our company name is Motion Claims Partners.

Industry/Entity Type

Physical Therapy

```html
<!DOCTYPE html>
<html lang="en">
<head>
<meta charset="utf-8">
<title>Motion Claims Partners Postcard</title>
<link rel="stylesheet" href="https://fonts.googleapis.com/css2?family=Alfa+Slab+One&family=Arimo:wght@400;700&family=Tinos&display=swap">
<style>
  :root {
    --page: #ecebe8;
    --card: #ffffff;
    --blue: #1b5fa6;
    --green: #3ea642;
    --green-bright: #4cb748;
    --ink: #222222;
    --muted: #a5a5a5;
    --dark: #1c1a19;
    --rule: #8a8a8a;
  }
  * { margin: 0; padding: 0; box-sizing: border-box; }
  html, body { width: 790px; height: 1200px; overflow: hidden; }
  body { background: var(--page); position: relative; font-family: "Arimo", Arial, sans-serif; color: var(--ink); }

  .card { position: absolute; left: 67px; width: 657px; height: 505px; background: var(--card); box-shadow: 0 4px 14px rgba(0,0,0,.25); overflow: hidden; }
  .card--back { top: 58px; }
  .card--front { top: 623px; background: var(--dark); }

  /* back */
  .why { position: absolute; left: 21px; top: 22px; width: 296px; }
  .why__title { color: var(--blue); font-size: 18.5px; font-weight: 700; margin-bottom: 10px; }
  .why p { font-size: 12.2px; line-height: 13.6px; text-align: justify; margin-bottom: 13.5px; }
  .why__label { color: var(--green); font-weight: 700; text-transform: uppercase; }

  .brand { position: absolute; display: flex; align-items: center; gap: 8px; font-weight: 700; color: var(--blue); }
  .brand__dot { border-radius: 50%; background: var(--green); }
  .card--back .brand { left: 345px; top: 24px; font-size: 24px; }
  .card--back .brand__dot { width: 26px; height: 26px; }

  .contact { position: absolute; left: 347px; top: 76px; font-size: 13.5px; line-height: 17px; }
  .contact b { font-weight: 700; }

  .mail-label { position: absolute; font-family: "Tinos", serif; color: var(--muted); font-size: 13px; }
  .postage-label { left: 547px; top: 12px; }
  .postage-box { position: absolute; left: 554px; top: 32px; width: 69px; height: 78px; border: 1px solid var(--ink); }
  .address-label { left: 433px; top: 217px; }
  .address-line { position: absolute; left: 373px; width: 215px; border-top: 1px solid var(--rule); }
  .barcode-label { left: 367px; top: 467px; }

  /* front */
  .photo { position: absolute; left: 0; top: 0; width: 440px; height: 410px;
    background: radial-gradient(ellipse at 45% 55%, #8a6450 0%, #5a3c32 35%, #3a2c28 60%, #2a2624 100%); }
  .headline { position: absolute; left: 330px; width: 340px; top: 62px; text-align: center; font-family: "Alfa Slab One", Georgia, serif; }
  .headline__main { color: var(--green-bright); font-size: 46px; line-height: 56px; }
  .headline__sub { color: #fff; font-size: 17px; line-height: 28px; margin-top: 18px; }
  .headline__sub span { color: var(--green-bright); }
  .guarantee { position: absolute; left: 330px; width: 340px; top: 300px; text-align: center; color: #fff; font-weight: 700; font-size: 15px; line-height: 18.5px; }

  .base { position: absolute; left: 0; top: 0; }
  .card--front .brand { left: 60px; top: 412px; font-size: 32px; }
  .card--front .brand__dot { width: 32px; height: 32px; }
  .legal-name { position: absolute; left: 26px; top: 468px; color: var(--blue); font-weight: 700; font-size: 13px; }
  .cta { position: absolute; left: 278px; width: 380px; top: 406px; text-align: center; color: var(--blue); }
  .cta__line { font-size: 18px; line-height: 22px; }
  .cta__line b { font-weight: 700; }
  .cta__call { color: var(--green); font-weight: 700; font-size: 32px; line-height: 38px; }
</style>
</head>
<body>
  <section class="card card--back">
    <div class="why">
      <h2 class="why__title">Why MCP?</h2>
      <p><span class="why__label">Knowledge :</span> Our billers are trained exclusively in physical therapy billing and collections. MCP will work with the billing system you choose or are currently using. In addition, with one of our owners being a physical therapist herself, MCP has first-hand knowledge in choosing a PT software program that meets documentation standards and maximizes your collections.</p>
      <p><span class="why__label">Experience :</span> MCP is a physical therapy billing and consulting company with over 25 years of experience in managing physical therapy practices. We are experts in documentation and coding practices, and our billers are trained in Medicare and private payer guidelines and modifiers. MCP has the skills necessary to increase the efficiency and profitability of your clinic by taking the stress of billing and collections away from your staff, and allowing them to do what they do best – take care of patients!</p>
      <p><span class="why__label">Ancillary Income :</span> MCP can also improve your revenue by showing you how to develop additional services beyond standard physical therapy. We can develop a bracing and custom orthotics program for your clinic that enhances patient care and provides additional sources of revenue in a competitive marketplace.</p>
    </div>

    <div class="brand"><span class="brand__dot"></span>MCP</div>
    <div class="contact">
      <div><b>Phone:</b> 555-214-0187</div>
      <div><b>Email:</b> hi@mcpbilling.net</div>
    </div>

    <span class="mail-label postage-label">Postage Area</span>
    <div class="postage-box"></div>
    <span class="mail-label address-label">Address Area</span>
    <div class="address-line" style="top:241px"></div>
    <div class="address-line" style="top:280px"></div>
    <div class="address-line" style="top:319px"></div>
    <span class="mail-label barcode-label">Barcode Area</span>
  </section>

  <section class="card card--front">
    <div class="photo" role="img" aria-label="Photo of a stressed man holding his head as paperwork flies out of the top"></div>

    <div class="headline">
      <div class="headline__main">BILLING<br>ISSUES?</div>
      <div class="headline__sub">LET <span>MOTION CLAIMS<br>PARTNERS</span> RELIEVE<br>THOSE HEADACHES.</div>
    </div>
    <div class="guarantee">WE GUARANTEE AN INCREASE<br>IN YOUR COLLECTIONS<br>AND A DECREASE IN YOUR<br>ACCOUNTS RECEIVABLE.</div>

    <svg class="base" width="657" height="505" viewBox="0 0 657 505" aria-hidden="true">
      <path d="M0 405 L280 405 C320 405 340 397 400 397 L657 397 L657 505 L0 505 Z" fill="#ffffff"/>
    </svg>

    <div class="brand"><span class="brand__dot"></span>MCP</div>
    <div class="legal-name">MOTION CLAIMS PARTNERS LLC</div>

    <div class="cta">
      <div class="cta__line">Contact <b>MCP</b> today at</div>
      <div class="cta__line"><b>motionclaimspartners.net</b> or</div>
      <div class="cta__call">CALL : 555-214-0187</div>
    </div>
  </section>
</body>
</html>
```